Looking for a modern, Professional business card design

We have a simple business card, but are looking for a more modern, professional look. A sample of the basic card is attached as well as the logo. We would also like to add that we offer:
Struggling with your finances?
- Learn to become debt free
- Discover the power of cash
- Control your money instead of it controlling you
Let us help you achieve a new level of financial freedom!
Also, we would like to have a "SPECIAL OFFER!: FREE 30 minute consultation"
Financial Planning

```html
<!DOCTYPE html>
<html lang="en">
<head>
<meta charset="utf-8">
<title>Brightpath Coaching – Business Card</title>
<link rel="stylesheet" href="https://fonts.googleapis.com/css2?family=Open+Sans:wght@400;600;700&display=swap">
<style>
  :root {
    --page-bg: #ecebe8;
    --card-bg: #ffffff;
    --ink: #1f1f1f;
    --brand-green: #3c9a35;
    --icon-green: #4aa83c;
    --faint-green: #eef4ea;
    --rule: #2a2a2a;
  }
  * { margin: 0; padding: 0; box-sizing: border-box; }
  html, body { width: 1200px; height: 1000px; overflow: hidden; }
  body {
    background: var(--page-bg);
    font-family: "Open Sans", sans-serif;
    color: var(--ink);
    position: relative;
  }
  .card {
    position: absolute;
    left: 265px;
    width: 666px;
    height: 397px;
    background: var(--card-bg);
    box-shadow: 0 2px 6px rgba(0,0,0,0.18);
    overflow: hidden;
  }
  .card--front { top: 73px; }
  .card--back { top: 533px; }

  .brand {
    position: absolute;
    display: flex;
    align-items: center;
    gap: 12px;
  }
  .brand__dot {
    width: 30px; height: 30px;
    border-radius: 50%;
    background: var(--brand-green);
  }
  .brand__name {
    font-weight: 700;
    font-size: 30px;
    color: var(--brand-green);
    letter-spacing: 0.5px;
  }
  .card--front .brand { left: 34px; top: 60px; }
  .card--back .brand { left: 32px; top: 62px; }

  .watermark {
    position: absolute;
    left: 360px; top: 90px;
    width: 260px; height: 260px;
    border-radius: 50%;
    background: var(--faint-green);
  }

  .contact {
    position: absolute;
    left: 33px; top: 188px;
    list-style: none;
    font-size: 16px;
    line-height: 22.5px;
  }
  .contact__item { display: flex; align-items: center; gap: 4px; }
  .contact__icon { width: 15px; height: 15px; flex: none; }
  .address {
    position: absolute;
    left: 33px; top: 284px;
    font-size: 16px;
  }
  .divider {
    position: absolute;
    left: 33px; top: 316px;
    width: 273px; height: 1px;
    background: var(--rule);
  }
  .offer {
    position: absolute;
    left: 33px; top: 327px;
    font-size: 16px;
    line-height: 21px;
  }
  .offer__title { font-weight: 700; }

  .person {
    position: absolute;
    right: 33px; top: 190px;
    text-align: right;
  }
  .person__name {
    font-weight: 700;
    font-size: 24px;
    color: var(--brand-green);
    line-height: 32px;
  }
  .person__role { font-size: 16px; line-height: 20px; }

  .pitch {
    position: absolute;
    left: 342px; top: 198px;
    width: 300px;
    font-size: 16px;
    line-height: 20px;
  }
  .pitch__heading { font-weight: 700; margin-bottom: 11px; }
  .pitch__list { list-style: none; }
  .pitch__item { display: flex; gap: 4px; margin-bottom: 6px; }
  .pitch__tick { width: 16px; height: 16px; flex: none; margin-top: 2px; }
  .pitch__close { margin-top: 4px; }
</style>
</head>
<body>

<section class="card card--front">
  <div class="brand">
    <span class="brand__dot"></span>
    <span class="brand__name">Brightpath Coaching</span>
  </div>

  <div class="watermark" role="img" aria-label="Faint decorative brand shape"></div>

  <ul class="contact">
    <li class="contact__item">
      <svg class="contact__icon" viewBox="0 0 16 16"><rect x="4" y="1" width="8" height="14" rx="1.5" fill="var(--icon-green)"/><rect x="5.5" y="3" width="5" height="6" fill="#fff"/></svg>
      <span>+ 000 000 0000</span>
    </li>
    <li class="contact__item">
      <svg class="contact__icon" viewBox="0 0 16 16"><path d="M1 6c0-2 3-3 7-3s7 1 7 3v1h-4V5.5H5V7H1z" fill="var(--icon-green)"/><rect x="3" y="8" width="10" height="6" rx="1" fill="var(--icon-green)"/></svg>
      <span>+ 000 000 0000</span>
    </li>
    <li class="contact__item">
      <svg class="contact__icon" viewBox="0 0 16 16"><rect x="1" y="3" width="14" height="10" fill="var(--icon-green)"/><path d="M1 3l7 6 7-6" fill="none" stroke="#fff" stroke-width="1.3"/></svg>
      <span>info@brightpathcoaching.com</span>
    </li>
    <li class="contact__item">
      <svg class="contact__icon" viewBox="0 0 16 16"><circle cx="8" cy="8" r="7" fill="var(--icon-green)"/><path d="M1 8h14M8 1c-3 3-3 11 0 14M8 1c3 3 3 11 0 14" stroke="#fff" stroke-width="1" fill="none"/></svg>
      <span>www.brightpathcoaching.com</span>
    </li>
  </ul>
  <p class="address">48 Harbor 17 St, Queens, NY 1109</p>
  <div class="divider"></div>
  <div class="offer">
    <p class="offer__title">SPECIAL OFFER!:</p>
    <p>FREE 30 minute consultation</p>
  </div>

  <div class="person">
    <p class="person__name">Daniel Okafor</p>
    <p class="person__role">Managing Director</p>
  </div>
</section>

<section class="card card--back">
  <div class="brand">
    <span class="brand__dot"></span>
    <span class="brand__name">Brightpath Coaching</span>
  </div>

  <div class="pitch">
    <p class="pitch__heading">Struggling with your finances?</p>
    <ul class="pitch__list">
      <li class="pitch__item">
        <svg class="pitch__tick" viewBox="0 0 16 16"><path d="M2 8l4 5L14 3" fill="none" stroke="var(--icon-green)" stroke-width="2.2" stroke-linecap="round" stroke-linejoin="round"/></svg>
        <span>Learn to become debt free</span>
      </li>
      <li class="pitch__item">
        <svg class="pitch__tick" viewBox="0 0 16 16"><path d="M2 8l4 5L14 3" fill="none" stroke="var(--icon-green)" stroke-width="2.2" stroke-linecap="round" stroke-linejoin="round"/></svg>
        <span>Discover the power of cash</span>
      </li>
      <li class="pitch__item">
        <svg class="pitch__tick" viewBox="0 0 16 16"><path d="M2 8l4 5L14 3" fill="none" stroke="var(--icon-green)" stroke-width="2.2" stroke-linecap="round" stroke-linejoin="round"/></svg>
        <span>Control your money instead of it controlling you</span>
      </li>
    </ul>
    <p class="pitch__close">Let us help you achieve a new level of financial freedom!</p>
  </div>
</section>

</body>
</html>
```